Dog grooming business card
This is a business card for m dog grooming business like it say above.
In the priorities box below I will have the text that I want on the card.

Industry/Entity Type

Business

Colors

Designer to choose colors to be used in the design.

Requirements
Must have
• My logo and the insurance stamp must be on the card.

Text it must have :

Professional grooming services
Email: lunabrisk@mailvale.net
Text or call 1 705 318 6052
TWF certified/member
Pet first aid certified
Next appointment ___________________________________
Nice to have
• Greens to match my logo

```html
<!DOCTYPE html>
<html lang="en">
<head>
<meta charset="utf-8">
<title>Luna Brisk – Grooming Business Card</title>
<link href="https://fonts.googleapis.com/css2?family=Rokkitt:wght@500;600&display=swap" rel="stylesheet">
<style>
  :root {
    --bg: #ece8e1;
    --ink: #231f20;
    --green: #95c13d;
    --green-soft: #c6df8f;
    --paper: #ffffff;
    --badge-blue: #2f6db5;
    --text-font: "Rokkitt", Georgia, serif;
  }
  html, body {
    margin: 0;
    width: 1200px;
    height: 870px;
    overflow: hidden;
    background: var(--bg);
  }
  .stage {
    position: relative;
    width: 1200px;
    height: 870px;
  }
  .card {
    position: absolute;
    top: 67px;
    width: 420px;
    height: 735px;
    background: var(--paper);
    overflow: hidden;
    box-shadow: 0 6px 18px rgba(0,0,0,.18);
    font-family: var(--text-font);
    color: var(--ink);
  }
  .card--front { left: 150px; }
  .card--back  { left: 630px; }
  .card__shapes {
    position: absolute;
    inset: 0;
  }
  .brand-name {
    position: absolute;
    left: 0;
    right: 0;
    display: flex;
    align-items: center;
    justify-content: center;
    gap: 14px;
    font-family: var(--text-font);
    font-weight: 600;
    font-size: 58px;
    line-height: 1;
  }
  .brand-name__dot {
    width: 22px;
    height: 22px;
    border-radius: 50%;
  }
  .card--front .brand-name { top: 160px; color: var(--green); }
  .card--front .brand-name__dot { background: var(--green); }
  .card--back .brand-name { top: 110px; color: var(--ink); }
  .card--back .brand-name__dot { background: var(--green); }

  .details {
    position: absolute;
    top: 438px;
    left: 0;
    right: 0;
    margin: 0;
    padding: 0;
    list-style: none;
    text-align: center;
    font-weight: 600;
    font-size: 27px;
    line-height: 34px;
    letter-spacing: .3px;
  }
  .appointment {
    position: absolute;
    left: 26px;
    right: 24px;
    top: 650px;
    display: flex;
    align-items: flex-end;
    gap: 10px;
    font-weight: 600;
    font-size: 27px;
  }
  .appointment__line {
    flex: 1;
    border-bottom: 2px solid var(--ink);
    margin-bottom: 34px;
  }
  .insurance-badge {
    position: absolute;
    right: 22px;
    bottom: 22px;
    width: 108px;
    height: 46px;
    border: 2px solid var(--badge-blue);
    border-radius: 9px;
    background: var(--paper);
  }
  .symbol-decoration {
    position: absolute;
    left: 110px;
    top: 520px;
    width: 200px;
    height: 170px;
    border-radius: 100px 100px 90px 90px;
    background: radial-gradient(circle at 50% 45%, #ffffff 55%, var(--green-soft) 100%);
  }
</style>
</head>
<body>
<main class="stage">

  <section class="card card--front" aria-label="Business card front">
    <svg class="card__shapes" width="420" height="735" viewBox="0 0 420 735" aria-hidden="true">
      <ellipse cx="250" cy="95" rx="360" ry="305" fill="var(--green)"/>
      <ellipse cx="250" cy="70" rx="350" ry="300" fill="var(--ink)"/>
    </svg>
    <div class="brand-name"><span class="brand-name__dot"></span>Luna Brisk</div>
    <ul class="details">
      <li>Professional grooming services</li>
      <li>1 705 318 6052</li>
      <li>lunabrisk@mailvale.net</li>
      <li>TWF certified/member</li>
      <li>Pet first aid certified</li>
    </ul>
    <div class="appointment">
      <span>Next appointment</span>
      <span class="appointment__line"></span>
    </div>
    <div class="insurance-badge" role="img" aria-label="Insurance stamp"></div>
  </section>

  <section class="card card--back" aria-label="Business card back">
    <svg class="card__shapes" width="420" height="735" viewBox="0 0 420 735" aria-hidden="true">
      <path d="M0 225 C110 380 290 440 420 420 V735 H0 Z" fill="var(--green)"/>
      <path d="M0 195 C110 360 290 420 420 395 V422 C290 442 110 382 0 228 Z" fill="var(--ink)"/>
    </svg>
    <div class="brand-name"><span class="brand-name__dot"></span>Luna Brisk</div>
    <div class="symbol-decoration" role="img" aria-label="Brand symbol decoration area"></div>
  </section>

</main>
</body>
</html>
```